Velmora Battery Saver App UI design.

We need a mockup layout design of an Velmora app uncoded. This simple battery saver app is composed primarily by three screens described in the attached specification. After the mockup approved we need the UI elements sliced, the app icon and a banner for the nook mart.

```html
<!DOCTYPE html>
<html lang="en">
<head>
<meta charset="utf-8">
<title>Velmora Battery Saver – Power Management</title>
<link rel="stylesheet" href="https://fonts.googleapis.com/css2?family=Raleway:wght@300;400;500&family=Roboto:wght@400;500&display=swap">
<style>
  :root {
    --bg-top: #566c84;
    --bg-bottom: #1c2630;
    --green: #3dbd74;
    --green-dark: #2fa862;
    --teal: #1aa3b8;
    --tile: #2b2827;
    --tile-alt: #262322;
    --divider: #1a1817;
    --screen: #211f1e;
    --white: #f4f4f2;
    --grey-knob: #8a8d8f;
    --text-light: #e9e9e7;
    --tab-text: #1e9fb0;
  }
  * { box-sizing: border-box; margin: 0; padding: 0; }
  html, body { width: 1200px; height: 962px; overflow: hidden; }
  body {
    background: linear-gradient(160deg, var(--bg-top) 0%, var(--bg-bottom) 100%);
    font-family: "Raleway", sans-serif;
    position: relative;
  }
  .app-screen {
    position: absolute; left: 390px; top: 106px;
    width: 420px; height: 750px;
    background: var(--screen);
    overflow: hidden;
    box-shadow: 0 20px 60px rgba(0,0,0,.45);
  }
  .status-bar {
    height: 24px; background: var(--green-dark);
    display: flex; justify-content: flex-end; align-items: center; gap: 6px;
    padding-right: 10px; color: var(--white);
    font-family: "Roboto", sans-serif; font-size: 13px;
  }
  .toolbar {
    height: 56px; background: var(--green);
    display: flex; align-items: center; gap: 14px; padding-left: 16px;
    color: var(--white); font-family: "Roboto", sans-serif; font-size: 20px;
  }
  .app-mark { width: 26px; height: 26px; background: var(--white); border-radius: 4px; }
  .tabs {
    height: 44px; background: var(--white);
    display: flex; font-size: 13px; letter-spacing: .5px; color: var(--tab-text);
  }
  .tab { flex: 1; display: flex; align-items: center; justify-content: center; position: relative; }
  .tab.active { color: var(--green); }
  .tab.active::after {
    content: ""; position: absolute; left: 0; right: 0; bottom: 0; height: 3px; background: var(--green);
  }
  .toggle-grid { display: grid; grid-template-columns: 1fr 1fr; gap: 2px; background: var(--divider); }
  .toggle-tile {
    height: 130px; background: var(--tile); position: relative;
  }
  .toggle-tile .tile-icon { position: absolute; left: 28px; top: 26px; }
  .toggle-tile .switch { position: absolute; right: 20px; top: 24px; }
  .tile-label {
    position: absolute; left: 0; right: 0; bottom: 0; height: 30px;
    background: var(--teal); color: var(--text-light);
    font-size: 14px; letter-spacing: 1px; text-align: center; line-height: 30px;
  }
  .switch {
    width: 68px; height: 30px; border-radius: 15px; background: var(--white);
    position: relative; font-family: "Roboto", sans-serif; font-size: 11px; color: #555;
  }
  .switch .knob {
    position: absolute; top: 3px; width: 24px; height: 24px; border-radius: 50%;
  }
  .switch.on .knob { right: 4px; background: var(--green); }
  .switch.on .state { position: absolute; left: 12px; top: 8px; }
  .switch.off .knob { left: 4px; background: var(--grey-knob); }
  .switch.off .state { position: absolute; right: 14px; top: 8px; }
  .control-row {
    height: 80px; background: var(--tile-alt); border-top: 2px solid var(--divider);
    display: flex; align-items: center; padding: 0 24px; gap: 16px;
    color: var(--text-light); font-size: 14px; letter-spacing: 1px;
  }
  .control-row .row-label { width: 120px; }
  .slider { flex: 1; height: 3px; background: #d7d7d5; position: relative; }
  .slider .fill { position: absolute; left: 0; top: 0; bottom: 0; background: var(--green); }
  .slider .thumb {
    position: absolute; top: -7px; width: 16px; height: 16px; border-radius: 50%;
    background: var(--green); margin-left: -8px;
  }
  .mode-panel {
    height: 150px; background: var(--tile); border-top: 2px solid var(--divider);
    display: flex; align-items: center; padding: 0 34px; gap: 60px;
    color: var(--text-light); font-size: 14px; letter-spacing: 1px;
  }
  .mode-control { display: flex; flex-direction: column; align-items: center; gap: 14px; }
  .nav-bar {
    position: absolute; left: 0; right: 0; bottom: 0; height: 56px; background: #1b1918;
    display: flex; justify-content: space-around; align-items: center;
  }
</style>
</head>
<body>
<main class="app-screen">
  <div class="status-bar">
    <svg width="16" height="12" viewBox="0 0 16 12"><path d="M8 12 0 3a12 12 0 0 1 16 0z" fill="#fff"/></svg>
    <svg width="12" height="12" viewBox="0 0 12 12"><path d="M12 0v12H0z" fill="#fff"/></svg>
    <svg width="8" height="13" viewBox="0 0 8 13"><rect x="0" y="1" width="8" height="12" rx="1" fill="#fff"/><rect x="2" y="0" width="4" height="2" fill="#fff"/></svg>
    <span class="clock">12:06</span>
  </div>
  <header class="toolbar">
    <span class="app-mark"></span>
    <h1 class="app-title" style="font-size:20px;font-weight:400">Charge Keeper Next!</h1>
  </header>
  <nav class="tabs">
    <div class="tab">CURRENT INFO</div>
    <div class="tab active">POWER MANAGEMENT</div>
  </nav>

  <section class="toggle-grid">
    <div class="toggle-tile">
      <svg class="tile-icon" width="50" height="44" viewBox="0 0 50 44" fill="none" stroke="#fff" stroke-width="5" stroke-linecap="round">
        <path d="M4 16a30 30 0 0 1 42 0"/><path d="M12 25a19 19 0 0 1 26 0"/><path d="M19 33a8 8 0 0 1 12 0"/><circle cx="25" cy="40" r="2" fill="#fff"/>
      </svg>
      <div class="switch on"><span class="state">On</span><span class="knob"></span></div>
      <div class="tile-label">WIFI</div>
    </div>
    <div class="toggle-tile">
      <svg class="tile-icon" width="44" height="44" viewBox="0 0 44 44" fill="#fff">
        <path d="M4 18 16 6v7h14v10H16v7z"/><path d="M40 26 28 38v-7H14V21h14v-7z" opacity=".9"/>
      </svg>
      <div class="switch off"><span class="knob"></span><span class="state">Off</span></div>
      <div class="tile-label">DATA</div>
    </div>
    <div class="toggle-tile">
      <svg class="tile-icon" width="30" height="46" viewBox="0 0 30 46" fill="none" stroke="#fff" stroke-width="3.5" stroke-linejoin="round">
        <path d="M4 14 24 32 14 42V4l10 10L4 32"/>
      </svg>
      <div class="switch on"><span class="state">On</span><span class="knob"></span></div>
      <div class="tile-label">BLUETOOTH</div>
    </div>
    <div class="toggle-tile">
      <svg class="tile-icon" width="50" height="44" viewBox="0 0 50 44" fill="none" stroke="#fff" stroke-width="3" stroke-linecap="round">
        <rect x="15" y="4" width="20" height="36" rx="3"/><path d="M8 14v16M3 18v8M42 14v16M47 18v8"/>
      </svg>
      <div class="switch on"><span class="state">On</span><span class="knob"></span></div>
      <div class="tile-label">VIBRATE</div>
    </div>
  </section>

  <section class="control-row">
    <svg width="40" height="40" viewBox="0 0 40 40" fill="none" stroke="#fff" stroke-width="2.5" stroke-linecap="round">
      <path d="M14 26a9 9 0 1 1 12 0v5H14z"/><path d="M15 35h10M20 2v4M5 8l3 3M35 8l-3 3M1 20h4M35 20h4"/>
    </svg>
    <span class="row-label">BRIGHTNESS</span>
    <div class="slider"><span class="fill" style="width:38%"></span><span class="thumb" style="left:38%"></span></div>
  </section>
  <section class="control-row">
    <svg width="40" height="40" viewBox="0 0 40 40" fill="#fff">
      <path d="M4 14h8l12-10v32L12 26H4z"/><path d="M29 12a11 11 0 0 1 0 16M33 7a17 17 0 0 1 0 26" fill="none" stroke="#fff" stroke-width="3" stroke-linecap="round"/>
    </svg>
    <span class="row-label">VOLUME</span>
    <div class="slider"><span class="fill" style="width:72%"></span><span class="thumb" style="left:72%"></span></div>
  </section>

  <section class="mode-panel">
    <svg width="86" height="86" viewBox="0 0 86 86" fill="none" stroke="#fff" stroke-width="5">
      <ellipse cx="43" cy="43" rx="40" ry="15"/>
      <ellipse cx="43" cy="43" rx="40" ry="15" transform="rotate(60 43 43)"/>
      <ellipse cx="43" cy="43" rx="40" ry="15" transform="rotate(-60 43 43)"/>
      <circle cx="43" cy="43" r="5" fill="#fff" stroke="none"/>
    </svg>
    <div class="mode-control">
      <span class="row-label">INTELLIGENT MODE</span>
      <div class="switch off"><span class="knob"></span><span class="state">Off</span></div>
    </div>
  </section>

  <footer class="nav-bar">
    <svg width="30" height="22" viewBox="0 0 30 22" fill="none" stroke="#fff" stroke-width="2.5" stroke-linecap="round" stroke-linejoin="round">
      <path d="M9 4 3 10l6 6"/><path d="M3 10h16a7 7 0 0 1 0 14h-6" transform="translate(0 -3)"/>
    </svg>
    <svg width="32" height="22" viewBox="0 0 32 22" fill="none" stroke="#fff" stroke-width="2.5" stroke-linejoin="round">
      <path d="M2 20V10L16 2l14 8v10z"/>
    </svg>
    <svg width="28" height="24" viewBox="0 0 28 24" fill="none" stroke="#fff" stroke-width="2.5">
      <rect x="2" y="8" width="20" height="14"/><path d="M7 4h18v14"/>
    </svg>
  </footer>
</main>
</body>
</html>
```